Wholesale in Gold Jewellery & Gold Bullion

We are an established gold jewellery and gold bullion wholesaler selling these products to international clients. We already have a name and logo of our company, hence please view attached current card design. We need a completely new design to compliment our business and industry and the final design should be new and elegant.

Contact Information for Business Card

New card details must be same as per current card. Like logo, name, tel no. & etc.

Colors

Designer to choose colors to be used in the design.

```html
<!DOCTYPE html>
<html lang="en">
<head>
<meta charset="utf-8">
<title>Karan &amp; Co Business Card</title>
<link href="https://fonts.googleapis.com/css2?family=Roboto+Slab:wght@500;700&family=Open+Sans:wght@400;700&family=Questrial&display=swap" rel="stylesheet">
<style>
  :root {
    --backdrop: #e6e6e8;
    --card-white: #ffffff;
    --gold: #d99511;
    --ink: #3b3b3b;
    --rule-grey: #a9a9a9;
    --on-gold: #ffffff;
    --rule-gold: rgba(255, 255, 255, 0.85);
    --divider-gold: #e9b24a;
  }
  * { margin: 0; padding: 0; box-sizing: border-box; }
  html, body {
    width: 1200px;
    height: 900px;
    overflow: hidden;
    background: var(--backdrop);
  }
  .stage { position: relative; width: 1200px; height: 900px; }

  .card {
    position: absolute;
    width: 560px;
    height: 320px;
    border-radius: 28px;
    display: flex;
    flex-direction: column;
    align-items: center;
    justify-content: center;
    text-align: center;
  }

  /* Front: white card */
  .card-front {
    left: 90px;
    top: 110px;
    background: var(--card-white);
    color: var(--ink);
  }
  .brand-mark {
    width: 74px;
    height: 74px;
    border-radius: 50%;
    background: var(--gold);
    margin-bottom: 14px;
  }
  .brand-name {
    font-family: "Roboto Slab", Georgia, serif;
    font-weight: 700;
    font-size: 38px;
    letter-spacing: 1px;
    line-height: 1;
  }
  .brand-suffix {
    display: flex;
    align-items: center;
    gap: 10px;
    width: 300px;
    margin-top: 4px;
    font-family: "Roboto Slab", Georgia, serif;
    font-weight: 700;
    font-size: 10px;
    letter-spacing: 2px;
  }
  .brand-suffix::before,
  .brand-suffix::after {
    content: "";
    flex: 1;
    height: 1px;
    background: var(--rule-grey);
  }
  .card-front .brand-suffix { color: var(--ink); }
  .address {
    margin-top: 34px;
    font-family: "Questrial", Arial, sans-serif;
    font-size: 16px;
    letter-spacing: 0.3px;
  }

  /* Back: gold card */
  .card-back {
    left: 550px;
    top: 470px;
    background: var(--gold);
    color: var(--on-gold);
  }
  .card-back .brand-name { font-size: 40px; }
  .card-back .brand-suffix::before,
  .card-back .brand-suffix::after { background: var(--rule-gold); }
  .person-name {
    margin-top: 24px;
    font-family: "Roboto Slab", Georgia, serif;
    font-weight: 700;
    font-size: 19px;
    letter-spacing: 1px;
  }
  .person-role {
    font-family: "Open Sans", Arial, sans-serif;
    font-size: 14px;
    margin-top: 2px;
  }
  .divider {
    width: 330px;
    height: 1px;
    background: var(--divider-gold);
    margin: 14px 0 12px;
  }
  .contact {
    font-family: "Open Sans", Arial, sans-serif;
    font-size: 15px;
    line-height: 1.45;
  }
  .contact b { font-weight: 700; }
</style>
</head>
<body>
<main class="stage">
  <section class="card card-front" aria-label="Business card front">
    <div class="brand-mark" aria-hidden="true"></div>
    <div class="brand-name">KARAN &amp; CO</div>
    <div class="brand-suffix">PTE LTD</div>
    <p class="address">52 Lower Cane Rd, Singapore 208815</p>
  </section>

  <section class="card card-back" aria-label="Business card back">
    <div class="brand-name">KARAN &amp; CO</div>
    <div class="brand-suffix">PTE LTD</div>
    <p class="person-name">ARVIND MENON</p>
    <p class="person-role">Director</p>
    <div class="divider"></div>
    <p class="contact"><b>P:</b> +65 6100 2000 | <b>M:</b> +65 9100 4321</p>
    <p class="contact"><b>F:</b> +65 6100 2001 | <b>E:</b> arvind@karanco.com</p>
  </section>
</main>
</body>
</html>
```